Business Card Design Project

Business Card
We are rebranding with a new logo
Industry/Entity Type
Business
Contact Information for Business Card
Dennis Morvale +61 487215963 dennis@quorv.com.au P.O. Box 872 Fernlow QLD 4309
Requirements
Must have
- Logo

```html
<!DOCTYPE html>
<html lang="en">
<head>
<meta charset="UTF-8">
<title>Quorv International – Business Card</title>
<link href="https://fonts.googleapis.com/css2?family=Roboto:wght@400;700&family=Yellowtail&display=swap" rel="stylesheet">
<style>
  :root {
    --page-bg: #e6e6e6;
    --blue-deep: #054a6a;
    --blue-mid: #0277a8;
    --blue-bright: #04a2db;
    --card-white: #f7f7f7;
    --ink: #1a1a1a;
    --ink-blue: #0c4f70;
    --accent-orange: #e0621c;
    --white: #ffffff;
  }
  * { margin: 0; padding: 0; box-sizing: border-box; }
  html, body {
    width: 1200px; height: 576px; overflow: hidden;
    background: var(--page-bg);
  }
  .canvas { position: relative; width: 1200px; height: 576px; }
  .card {
    position: absolute; width: 483px; height: 292px;
    border-radius: 14px;
    box-shadow: 0 3px 6px rgba(0,0,0,0.18);
  }
  .card-front {
    left: 82px; top: 139px;
    background: linear-gradient(90deg, var(--blue-deep) 0%, var(--blue-mid) 45%, var(--blue-bright) 100%);
    display: flex; align-items: center; justify-content: center;
  }
  .card-back { left: 602px; top: 138px; background: var(--card-white); }
  .brand {
    font-family: "Roboto", sans-serif; font-weight: 700;
    text-align: center; line-height: 1;
  }
  .brand-front { color: var(--white); margin-top: -20px; }
  .brand-back {
    position: absolute; right: 34px; top: 44px;
    color: var(--ink-blue);
  }
  .brand-name { display: block; letter-spacing: 1px; }
  .brand-front .brand-name { font-size: 60px; }
  .brand-back .brand-name { font-size: 44px; }
  .brand-sub { display: block; letter-spacing: 3px; margin-top: 8px; }
  .brand-front .brand-sub { font-size: 16px; }
  .brand-back .brand-sub { font-size: 12px; margin-top: 7px; }
  .holder { position: absolute; left: 25px; top: 40px; }
  .holder-name {
    font-family: "Yellowtail", cursive; font-size: 26px;
    color: var(--ink-blue); line-height: 1;
  }
  .holder-title {
    font-family: "Roboto", sans-serif; font-size: 11.5px;
    color: var(--ink); margin-top: 6px;
  }
  .contacts {
    position: absolute; left: 28px; top: 214px;
    list-style: none;
    font-family: "Roboto", sans-serif; font-size: 12.5px; color: var(--ink);
  }
  .contacts li { display: flex; align-items: center; height: 17px; }
  .contacts svg { width: 12px; height: 12px; margin-right: 12px; fill: var(--accent-orange); }
</style>
</head>
<body>
<div class="canvas">
  <section class="card card-front">
    <div class="brand brand-front">
      <span class="brand-name">Quorv</span>
      <span class="brand-sub">INTERNATIONAL</span>
    </div>
  </section>

  <section class="card card-back">
    <div class="holder">
      <p class="holder-name">Dennis Morvale</p>
      <p class="holder-title">Managing Director</p>
    </div>
    <div class="brand brand-back">
      <span class="brand-name">Quorv</span>
      <span class="brand-sub">INTERNATIONAL</span>
    </div>
    <ul class="contacts">
      <li>
        <svg viewBox="0 0 12 12" aria-hidden="true"><path d="M1 4.5C1 2.5 3 1.5 6 1.5s5 1 5 3v1H8.5V4H3.5v1.5H1z"/><path d="M2.5 6.5h7l1 4.5h-9z"/></svg>
        +61 487215963
      </li>
      <li>
        <svg viewBox="0 0 12 12" aria-hidden="true"><path d="M1 2.5h10v7H1z M1.6 3.2 6 6.6l4.4-3.4" stroke="#f7f7f7" stroke-width="0.8"/></svg>
        dennis@quorv.com.au
      </li>
      <li>
        <svg viewBox="0 0 12 12" aria-hidden="true"><path d="M6 0.5a4 4 0 0 1 4 4c0 3-4 7-4 7s-4-4-4-7a4 4 0 0 1 4-4zm0 2.3a1.7 1.7 0 1 0 0 3.4 1.7 1.7 0 0 0 0-3.4z"/></svg>
        P.O. Box 872 Fernlow QLD 4309
      </li>
    </ul>
  </section>
</div>
</body>
</html>
```